Harrowmere Freight, Project

Company Profile
Harrowmere Freight Sdn Bhd is a well established and experienced freight forwarder in Kuala Lumpur, Malaysia. We specialize in air and sea forwarding, Custom Brokerage and regulatory compliance services, inland transportation,
overseas freighting and warehousing and distribution management. With our dedicated qualified and experienced professionals, we are fully committed to serving our clients.

Our Mission
Based on the motto “Quick, Reliable and Polite”, Harrowmere Freight is dedicated to upholding the following three points corporate philosophy:
1. Adhering to the principle that “the customer always comes first”.
2. Contributing to the development of the local community.
3. Making it our duty to be responsible and sincere.

Our Edge
• One-Stop Logistics Solutions
• Extensive Network Throughout Malaysia
• Highly Qualified and Experienced Pool of Professionals
• Comprehensive IT Solutions
• Innovative and Customer-focused Solutions
• Flexible and Consistent in Managing Exceptions
• Total Supply Chain Visibility

Target Market(s)

We sell the logistics services to all the industry in Malaysia. (ONE Stop Logistics Solutions)

Industry/Entity Type

Logistic

Contact Information for Business Card

I want the back of the card to be white with the logo and slogan. i would like to see the logo on the front with the general info.

Requirements
Must have
• Name, Title, Office, Cell, Fax, Email, Address, Website
Nice to have
• Modern Design Business Card

```html
<!DOCTYPE html>
<html lang="en">
<head>
<meta charset="utf-8">
<title>Harrowmere Freight – Business Card</title>
<link href="https://fonts.googleapis.com/css2?family=Open+Sans:wght@400;600;700&display=swap" rel="stylesheet">
<style>
  :root {
    --brand-blue: #3a9bd9;
    --brand-blue-deep: #1f7fc2;
    --ink: #4a4a4a;
    --ink-dark: #2e2e2e;
    --paper: #ffffff;
    --backdrop: #e9ebee;
  }
  * { box-sizing: border-box; margin: 0; padding: 0; }
  html, body {
    width: 1200px; height: 950px; overflow: hidden;
    background: var(--backdrop);
    font-family: "Open Sans", Arial, sans-serif;
  }
  .stage { position: relative; width: 1200px; height: 950px; }
  .card {
    position: absolute; left: 240px; width: 720px; height: 410px;
    box-shadow: 0 6px 18px rgba(0,0,0,.18);
    overflow: hidden;
  }
  /* Back of card */
  .card-back { top: 40px; background: var(--brand-blue); color: var(--paper); }
  .back-brand {
    position: absolute; left: 60px; top: 150px;
    display: flex; align-items: center; gap: 14px;
  }
  .brand-dot { width: 34px; height: 34px; border-radius: 50%; background: var(--paper); }
  .brand-name { font-size: 30px; font-weight: 600; color: var(--paper); }
  .slogan {
    position: absolute; left: 60px; top: 300px;
    font-size: 17px; font-weight: 600; letter-spacing: .3px;
  }
  .services { position: absolute; left: 420px; top: 48px; }
  .services h2 { font-size: 17px; font-weight: 700; margin-bottom: 6px; }
  .services ul { list-style: none; font-size: 14px; line-height: 21px; }
  .services li::before { content: "•"; margin-right: 7px; }
  .services .pair::before { content: "•"; }
  .services .inner-dot { margin: 0 6px 0 14px; }

  /* Front of card */
  .card-front { top: 500px; background: var(--paper); color: var(--ink); }
  .name-band {
    position: absolute; left: 0; top: 110px; width: 500px; height: 96px;
    background: var(--brand-blue);
    color: var(--paper);
    padding: 22px 0 0 40px;
  }
  .person-name { font-size: 24px; font-weight: 700; line-height: 1.2; }
  .person-title { font-size: 15px; font-weight: 400; }
  .front-brand {
    position: absolute; right: 40px; top: 70px;
    display: flex; align-items: center; gap: 10px;
  }
  .front-brand .brand-dot { background: var(--brand-blue); width: 26px; height: 26px; }
  .front-brand .brand-name { color: var(--ink-dark); font-size: 26px; font-weight: 600; }
  .address {
    position: absolute; right: 40px; top: 228px; text-align: right;
    font-size: 13.5px; line-height: 20px;
  }
  .address .company { font-weight: 700; color: var(--ink-dark); }
  .contacts {
    position: absolute; left: 40px; top: 290px;
    list-style: none; font-size: 14px; line-height: 21px;
  }
  .contacts .label { color: var(--brand-blue-deep); font-weight: 700; }
</style>
</head>
<body>
<main class="stage">
  <section class="card card-back" aria-label="Card back">
    <div class="back-brand">
      <span class="brand-dot"></span>
      <span class="brand-name">Harrowmere Freight</span>
    </div>
    <p class="slogan">ONE STOP LOGISTICS SOLUTIONS</p>
    <div class="services">
      <h2>We're Specialize In</h2>
      <ul>
        <li>International Shipping (Air / Sea)</li>
        <li>Consolidation - NVOCC</li>
        <li>Project Management</li>
        <li>Supply Chain Management</li>
        <li>Tax Exemption Consultancy</li>
        <li>Custom Brokerage</li>
        <li>Transportation / Haulage</li>
        <li>Warehousing<span class="inner-dot">•</span>Packing</li>
        <li>Marine Insurance</li>
        <li>Distribution<span class="inner-dot">•</span>Door to Door</li>
      </ul>
    </div>
  </section>

  <section class="card card-front" aria-label="Card front">
    <div class="front-brand">
      <span class="brand-dot"></span>
      <span class="brand-name">Harrowmere Freight</span>
    </div>
    <div class="name-band">
      <p class="person-name">Daniel Rahmat</p>
      <p class="person-title">Managing Director</p>
    </div>
    <address class="address">
      <span class="company">HARROWMERE FREIGHT SDN. BHD. (1204418-K)</span><br>
      No. 18B, 2nd Floor, Jalan Seri Pantai 3C<br>
      Taman Kenanga 2, 41050 Klang<br>
      Selangor Darul Ehsan, Malaysia.
    </address>
    <ul class="contacts">
      <li><span class="label">P:</span> (603) 5521 3804 / 3805</li>
      <li><span class="label">M:</span> +6012-418 2270</li>
      <li><span class="label">F:</span> (603) 5521 3809</li>
      <li>daniel.rahmat@harrowmere.com.my</li>
      <li>www.harrowmere.com.my</li>
    </ul>
  </section>
</main>
</body>
</html>
```